Telecommunications/Power civil contractor needs business card design

Were a new telecommunications/power underground civil contractor that is looking for a new business card design. Our company colours are silver or grey and orange. Feel free to use the white background logo or the black background logo.

Target Market(s)

Local contractors, utility companies, private sector mining/energy companies, developers.

Industry/Entity Type

Telecommunications

Contact Information for Business Card

Each card will need the following info:
Persons name:
Title:
E-mail:
Phone number:
Shop Address:
Mailing Address:

Requirements
Must have
• Each card will need the following info:
• Persons name:
• Title:
• E-mail:
• Phone number:
• Shop Address:
• Mailing Address:

```html
<!DOCTYPE html>
<html lang="en">
<head>
<meta charset="utf-8">
<title>Delve Line Contracting Inc – Business Card</title>
<link rel="stylesheet" href="https://fonts.googleapis.com/css2?family=Open+Sans:wght@400;600;700;800&display=swap">
<style>
  :root {
    --stage: #e8e5e1;
    --card-black: #111111;
    --brand-orange: #f05a22;
    --silver-light: #e6e6e6;
    --silver-mid: #a7a7a7;
    --silver-dark: #5f5f5f;
    --ink: #111111;
    --white: #ffffff;
  }
  * { box-sizing: border-box; margin: 0; padding: 0; }
  html, body { width: 1200px; height: 675px; overflow: hidden; }
  body {
    background: var(--stage);
    font-family: "Open Sans", Arial, sans-serif;
    position: relative;
  }
  .card {
    position: absolute;
    top: 187px;
    width: 520px;
    height: 300px;
    border-radius: 20px;
    overflow: hidden;
    background: var(--card-black);
    box-shadow: 0 10px 24px rgba(0,0,0,0.25);
  }
  .card--back { left: 60px; }
  .card--front { left: 620px; }

  .brand {
    position: absolute;
    display: flex;
    flex-direction: column;
    align-items: center;
    text-align: center;
  }
  .brand__mark {
    width: 58px; height: 58px;
    border-radius: 50%;
    background: var(--silver-mid);
    margin-bottom: 10px;
  }
  .brand__name {
    color: var(--brand-orange);
    font-weight: 800;
    text-transform: uppercase;
    line-height: 1.05;
  }
  .card--back .brand { left: 0; right: 0; top: 78px; }
  .card--back .brand__name { font-size: 26px; }
  .card--back .brand__name small { display: block; font-size: 15px; letter-spacing: 0.06em; }

  .card--front .brand { left: 40px; width: 220px; top: 22px; }
  .card--front .brand__mark { width: 50px; height: 50px; margin-bottom: 8px; }
  .card--front .brand__name { font-size: 21px; }
  .card--front .brand__name small { display: block; font-size: 12px; letter-spacing: 0.06em; }

  .front-bands { position: absolute; inset: 0; }

  .person { position: absolute; left: 34px; top: 168px; }
  .person__name { color: var(--white); font-weight: 700; font-size: 16px; letter-spacing: 0.02em; }
  .person__title { color: var(--ink); font-size: 12px; margin-top: 1px; }

  .contact {
    position: absolute;
    left: 262px;
    top: 218px;
    color: var(--white);
    font-size: 12.5px;
    line-height: 1.35;
    list-style: none;
  }
  .contact__item { display: flex; align-items: center; gap: 6px; }
  .contact__item--address { display: block; padding-left: 20px; margin-bottom: 3px; }
  .contact__icon { width: 14px; height: 14px; flex: none; }
</style>
</head>
<body>

  <section class="card card--back" aria-label="Card back">
    <div class="brand">
      <div class="brand__mark"></div>
      <p class="brand__name">Delve Line<small>Contracting Inc</small></p>
    </div>
  </section>

  <section class="card card--front" aria-label="Card front">
    <svg class="front-bands" viewBox="0 0 520 300" width="520" height="300" aria-hidden="true">
      <defs>
        <linearGradient id="silverSweep" x1="0" y1="0" x2="1" y2="0">
          <stop offset="0" stop-color="var(--silver-dark)"/>
          <stop offset="0.45" stop-color="var(--silver-light)"/>
          <stop offset="1" stop-color="var(--silver-mid)"/>
        </linearGradient>
      </defs>
      <path d="M0 132 C 180 128, 360 168, 520 196 L520 214 C 360 188, 180 150, 0 150 Z" fill="url(#silverSweep)"/>
      <path d="M0 152 C 180 152, 360 190, 520 216 L520 224 C 360 200, 180 160, 0 158 Z" fill="var(--card-black)"/>
      <path d="M0 156 C 180 158, 360 198, 520 222 L520 300 L0 300 Z" fill="var(--brand-orange)"/>
    </svg>

    <div class="brand">
      <div class="brand__mark"></div>
      <p class="brand__name">Delve Line<small>Contracting Inc</small></p>
    </div>

    <div class="person">
      <p class="person__name">MARLOW KENT</p>
      <p class="person__title">Managing Director</p>
    </div>

    <ul class="contact">
      <li class="contact__item contact__item--address">N. 7 Cedar Row,<br>Suite 210, Tacoma, WA 98402</li>
      <li class="contact__item">
        <svg class="contact__icon" viewBox="0 0 16 16" aria-hidden="true">
          <path d="M2 6 C2 3, 14 3, 14 6 L11 7 L10 5.5 L6 5.5 L5 7 Z" fill="var(--ink)"/>
          <rect x="3" y="8" width="10" height="6" rx="1.5" fill="var(--ink)"/>
        </svg>
        <span>321.654.987</span>
      </li>
      <li class="contact__item">
        <svg class="contact__icon" viewBox="0 0 16 16" aria-hidden="true">
          <rect x="1.5" y="4" width="13" height="9" rx="1" fill="var(--ink)"/>
          <path d="M2 4.5 L8 9 L14 4.5" fill="none" stroke="var(--brand-orange)" stroke-width="1.2"/>
        </svg>
        <span>info@delvelinecontracting.com</span>
      </li>
    </ul>
  </section>

</body>
</html>
```